Need App for Impact Related Events

My app is to help with internal events. When you enter the prompted event code the next screen shows you everyone currently at the event. It will give you the ability to Start a conversation with someone you met at that event, or signal it is your turn to send a message. The next screen is a message thread with that person. I am looking for a design that incorporates the colors and ‘feel good’ emotion of our logo. I have pieced together a pretty good interpretation of what I’m looking for in the attached mockup by slicing and dicing designs. I also attached our logo mascot.Screens (see attached mockups)

Note 1: I do not like the picture on the screen used in screen one because it makes it seem like a dating app. I attached an alternative photo that can be used or present different ideas.

Note 2: On the login/signup screen (screen 2) I need an additional first and last name for login, you can try to fit this on one login screen or present a two step signup screen where that is presented in the second screen.

READ MOCKUP GUIDELINES UNDER Must Haves

Target Market(s)

People attending internal social impact events

Industry/Entity Type

Charity

Font styles to use
Sans Serif

Colors
86cfc6

Requirements
Must have
• Follow the screen mockups attached to project
• PLEASE READ
• I have provided a relatively close design of what I’m looking for in the mockups. Some screens need to be followed more closely to my design mockup than other. I have listed a guide below how how closely you should follow my mockup design exactly. Overall I would like to see some ideas of incorporating a few accent colors so it doesn’t appear SO Blue. I also attached some app inspiration designs I found from around the web
• Screen Mockup Guideline Follow %
• Screen 1: 65% - mostly on target, would like to see ways to make it not SO Blue and possibly creative places to add some explainer text describing the app
• Screen 2: 50% - general design idea is here, but more open
• Screen 3: 35% - a lot more room for design influence
• Screen 4: 70% - mostly on target, a little room for design influence/color scheme ideas
• Screen 5-6: 25% - a lot of room for design change/ideas/influence
• Screen 7-8: 80% - already very close to what I need, maybe open to slight sizing and color scheme ideas
• Screen 9: 15% - the most open for influence, only the general functionality of the screen is communicated here
Nice to have
• Please Read Mockup Guideline above. In large part I am looking for something to use some nice accent colors so it is not overwhelmingly blue and bring the whole design into a seamless style.
Should not have

```html
<!DOCTYPE html>
<html lang="en">
<head>
<meta charset="utf-8">
<title>Settings</title>
<link href="https://fonts.googleapis.com/css2?family=Mulish:wght@400;600;700;800&display=swap" rel="stylesheet">
<style>
  :root {
    --ink: #1f2230;
    --muted: #8a8d99;
    --body: #4a4d5a;
    --line: #ececf1;
    --bg: #ffffff;
    --teal: #86cfc6;
    --teal-deep: #3fa99c;
    --violet: #9a7ce6;
    --avatar: #b9b2ad;
  }
  * { margin: 0; padding: 0; box-sizing: border-box; }
  html, body { width: 675px; height: 1200px; overflow: hidden; background: var(--bg); }
  body { font-family: 'Mulish', sans-serif; color: var(--ink); position: relative; }
  .abs { position: absolute; }
  .page-title { left: 30px; top: 36px; font-size: 50px; font-weight: 800; letter-spacing: -0.5px; line-height: 1.2; }
  .avatar { border-radius: 50%; background: radial-gradient(circle at 50% 40%, #d9d3cf, var(--avatar) 70%); }
  .avatar--header { left: 578px; top: 36px; width: 58px; height: 58px; }
  .section-title { left: 30px; font-size: 36px; font-weight: 700; line-height: 1.2; }
  .divider { left: 0; width: 675px; height: 2px; background: var(--line); }
  .avatar--profile { left: 40px; top: 254px; width: 66px; height: 66px; }
  .profile-name { left: 134px; top: 253px; font-size: 28px; font-weight: 700; line-height: 1.2; }
  .profile-tagline { left: 134px; top: 299px; font-size: 24px; color: var(--muted); line-height: 1.2; }
  .edit-button { left: 488px; top: 250px; width: 154px; height: 72px; border-radius: 8px;
    background: linear-gradient(90deg, var(--teal-deep), var(--teal) 55%, var(--violet)); color: #fff;
    font-size: 24px; font-weight: 800; letter-spacing: 2px; display: flex; align-items: center; justify-content: center;
    box-shadow: 0 6px 14px rgba(63, 169, 156, 0.28); }
  .row-label { left: 40px; font-size: 30px; font-weight: 600; line-height: 1.2; }
  .row-hint { left: 40px; font-size: 26px; color: var(--body); line-height: 1.2; }
  .toggle { left: 517px; top: 522px; width: 113px; height: 40px; border: 2.5px solid var(--teal-deep); border-radius: 20px; }
  .toggle-knob { position: absolute; right: 5px; top: 4px; width: 28px; height: 28px; border-radius: 50%;
    background: linear-gradient(135deg, var(--teal-deep), var(--violet)); }
  .nav-icon { width: 50px; height: 50px; }
  .fab { left: 285px; top: 1084px; width: 104px; height: 104px; border-radius: 50%;
    background: linear-gradient(135deg, var(--teal-deep), var(--teal) 50%, var(--violet)); display: flex; align-items: center; justify-content: center; }
  .nav-dot { left: 598px; top: 1096px; width: 18px; height: 18px; border-radius: 50%;
    background: linear-gradient(135deg, var(--teal-deep), var(--violet)); }
</style>
</head>
<body>
  <h1 class="abs page-title">Settings</h1>
  <div class="abs avatar avatar--header" role="img" aria-label="User profile photo"></div>

  <h2 class="abs section-title" style="top:140px">Profile</h2>
  <div class="abs divider" style="top:208px"></div>

  <div class="abs avatar avatar--profile" role="img" aria-label="Profile photo of Daniel Foster"></div>
  <p class="abs profile-name">Daniel Foster</p>
  <p class="abs profile-tagline">Be Nice Be Kind</p>
  <div class="abs edit-button">EDIT</div>
  <div class="abs divider" style="top:363px"></div>

  <h2 class="abs section-title" style="top:394px">Other</h2>
  <div class="abs divider" style="top:458px"></div>

  <p class="abs row-label" style="top:522px">Notifications</p>
  <div class="abs toggle"><span class="toggle-knob"></span></div>
  <div class="abs divider" style="top:613px"></div>

  <p class="abs row-label" style="top:656px">Rate Us</p>
  <p class="abs row-hint" style="top:704px">Go to AppHub and rate the app if you like!</p>
  <div class="abs divider" style="top:777px"></div>

  <svg class="abs nav-icon" style="left:42px;top:1127px" viewBox="0 0 24 24" fill="none" stroke="#3fa99c" stroke-width="1.8" stroke-linecap="round">
    <rect x="3" y="4.5" width="18" height="16" rx="2"/><path d="M3 9.5h18M8 2.5v4M16 2.5v4"/>
  </svg>
  <svg class="abs nav-icon" style="left:177px;top:1127px" viewBox="0 0 24 24" fill="none" stroke="#3fa99c" stroke-width="1.8" stroke-linejoin="round">
    <path d="M12 4a8 8 0 1 0 4.2 14.8L20 20l-1.2-3.8A8 8 0 0 0 12 4z"/>
  </svg>
  <div class="abs fab">
    <svg width="44" height="44" viewBox="0 0 24 24" stroke="#fff" stroke-width="2" stroke-linecap="round"><path d="M12 4v16M4 12h16"/></svg>
  </div>
  <svg class="abs nav-icon" style="left:447px;top:1127px" viewBox="0 0 24 24" fill="none" stroke="#3fa99c" stroke-width="1.8" stroke-linejoin="round" stroke-linecap="round">
    <path d="M6 16V11a6 6 0 0 1 12 0v5l2 2H4z"/><path d="M10 21h4"/>
  </svg>
  <div class="abs nav-dot"></div>
  <svg class="abs nav-icon" style="left:582px;top:1127px" viewBox="0 0 24 24" fill="none" stroke="#3fa99c" stroke-width="1.8" stroke-linecap="round">
    <path d="M3 7h18M3 12h18M3 17h18"/>
    <circle cx="15" cy="7" r="2" fill="#fff"/><circle cx="8" cy="12" r="2" fill="#fff"/><circle cx="14" cy="17" r="2" fill="#fff"/>
  </svg>
</body>
</html>
```